New Innovative Counselling and psychotherapy Service needs Business Card design

Keep it simple and professional. On one side, just company name and logo (perhaps in all blue) and maybe a tag line.

On other side (all white) my name and Qualifications in centre

Industry/Entity Type

Health And Wellness

Contact Information for Business Card

Dara Whelby
Counsellor & Psychotherapist
BSc (Psychol.), BA, Dip. (Couns. & Psych.), PG.Cert (CBT), FGTrK, ONRE

I will also require Mobile no, Email and web site address of which I'll pass on to final designer.

Font styles to use
Sans Serif

Requirements
Must have
• My Logo Only and please use the colours in logo that is in it.
Should not have
• Any other images

```html
<!DOCTYPE html>
<html lang="en">
<head>
<meta charset="utf-8">
<title>Thrive Meadow – Business Card</title>
<link rel="stylesheet" href="https://fonts.googleapis.com/css2?family=Raleway:wght@400&family=Arimo:wght@400;700&display=swap">
<style>
  :root {
    --stage: #2c2c2c;
    --card-front: #f6f6f6;
    --card-back: #343537;
    --ink: #3a3a3a;
    --ink-soft: #4a4a4a;
    --rule: #8a8a8a;
    --brand-blue: #3fb0e8;
    --brand-green: #8fcf52;
    --back-text: #f2f2f2;
  }
  html, body {
    margin: 0;
    padding: 0;
    width: 1200px;
    height: 960px;
    overflow: hidden;
    background: var(--stage);
  }
  .stage {
    position: relative;
    width: 1200px;
    height: 960px;
  }
  .card {
    position: absolute;
    left: 322px;
    width: 598px;
    height: 342px;
    border-radius: 18px;
    overflow: hidden;
  }
  .card--front { top: 110px; background: var(--card-front); }
  .card--back { top: 493px; background: var(--card-back); }

  .brand {
    position: absolute;
    font-family: "Raleway", sans-serif;
    font-weight: 400;
    white-space: nowrap;
    margin: 0;
  }
  .card--front .brand {
    left: 258px;
    top: 44px;
    font-size: 30px;
    line-height: 40px;
    color: var(--ink);
    display: flex;
    align-items: center;
    gap: 16px;
  }
  .brand__dot {
    width: 56px;
    height: 56px;
    border-radius: 50%;
    background: var(--brand-blue);
    flex: none;
  }

  .person {
    position: absolute;
    left: 35px;
    top: 170px;
    font-family: "Arimo", sans-serif;
    color: var(--ink-soft);
  }
  .person__name {
    margin: 0;
    font-size: 24px;
    line-height: 28px;
    font-weight: 400;
    color: var(--brand-blue);
  }
  .person__name strong { font-weight: 700; }
  .person__role {
    margin: 4px 0 2px;
    font-size: 15px;
    line-height: 18px;
  }
  .person__quals {
    margin: 0;
    font-size: 12px;
    line-height: 15px;
  }

  .divider {
    position: absolute;
    left: 35px;
    right: 33px;
    top: 262px;
    height: 1px;
    background: var(--rule);
  }

  .contact {
    position: absolute;
    left: 35px;
    top: 275px;
    margin: 0;
    padding: 0;
    list-style: none;
    font-family: "Arimo", sans-serif;
    font-size: 14px;
    line-height: 19px;
    color: var(--ink-soft);
  }
  .contact li { display: flex; align-items: center; gap: 7px; }
  .contact svg { flex: none; }
  .website {
    position: absolute;
    right: 32px;
    top: 294px;
    font-family: "Arimo", sans-serif;
    font-size: 14px;
    line-height: 19px;
    color: var(--ink-soft);
  }
  .edge-band {
    position: absolute;
    left: 0;
    bottom: 0;
    width: 598px;
    height: 11px;
  }

  .card--back .brand {
    right: 50px;
    top: 242px;
    font-size: 32px;
    line-height: 40px;
    color: var(--back-text);
  }
  .tagline {
    position: absolute;
    left: 282px;
    width 300px;
    top: 284px;
    width: 300px;
    margin: 0;
    text-align: center;
    font-family: "Arimo", sans-serif;
    font-size: 14px;
    line-height: 18px;
    color: var(--back-text);
  }
</style>
</head>
<body>
<main class="stage">
  <section class="card card--front" aria-label="Business card front">
    <p class="brand"><span class="brand__dot"></span>Thrive Meadow</p>

    <div class="person">
      <h1 class="person__name"><strong>Dara</strong> Whelby</h1>
      <p class="person__role">Counsellor &amp; Psychotherapist</p>
      <p class="person__quals">BSc (Psychol.), BA, Dip. (Couns. &amp; Psych.)<br>PG.Cert (CBT), FGTrK,</p>
    </div>

    <div class="divider"></div>

    <ul class="contact">
      <li>
        <svg width="12" height="16" viewBox="0 0 12 16" aria-hidden="true">
          <rect x="2" y="1" width="8" height="14" rx="1.5" fill="none" stroke="var(--brand-blue)" stroke-width="1.6"/>
          <rect x="4.5" y="12" width="3" height="1.2" fill="var(--brand-blue)"/>
        </svg>
        555 214 7089
      </li>
      <li>
        <svg width="12" height="10" viewBox="0 0 12 10" aria-hidden="true">
          <rect x="0.5" y="1" width="11" height="8" fill="var(--brand-blue)"/>
          <path d="M0.8 1.4 L6 5.6 L11.2 1.4" fill="none" stroke="#ffffff" stroke-width="1"/>
        </svg>
        dara@Thrivemeadow.com
      </li>
    </ul>
    <p class="website" style="margin:0">www.Thrivemeadow.com</p>

    <svg class="edge-band" viewBox="0 0 598 11" preserveAspectRatio="none" aria-hidden="true">
      <polygon points="0,0 340,0 336,11 0,11" fill="var(--brand-blue)"/>
      <polygon points="342,0 598,0 598,11 338,11" fill="var(--brand-green)"/>
    </svg>
  </section>

  <section class="card card--back" aria-label="Business card back">
    <p class="brand">Thrive Meadow</p>
    <p class="tagline">Caring For Your Psychological Well-Being<br>Is Our Top Priority</p>
  </section>
</main>
</body>
</html>
```